Hardcore nerd needs to stand out in a sea of dull Defence business cards

Wombarra Devices is a new Australian consulting engineering company that turns research and theory into practical systems. No evangelistic fluff, just mathematics and physics into electronic and optical circuits for consumer products, scientific research or Defence applications.

We already have a recognised logo (provided) which is often dark blue/black on a light background but we're open to other combinations. (Us engineers tend to have limited aesthetic imagination :)

Some of our recent products have included:
* Instrumentation for electrical testing,
* Radar jammers,
* GPS antenna design,
* Satellite tracking systems,
* High power lasers

We're open to both single and double-sided designs - happy to be convinced either way.

P.S. Another group is working on the web page, so - alas - our web site is currently of no use for images/ideas...

Target Market(s)

Engineering managers,
Scientists

Contact Information for Business Card

Dr Colin Harte
R&D Engineer

colin@wombarradevices.com.au
0427 563 710

PO Box XXX (to be confirmed)
Kelsby ACT 2917
Australia

Font styles to use
Serif
Sans Serif

Colors

Designer to choose colors to be used in the design.

Requirements
Must have
• My contact details!
• I've had many (great) "bold and plain" designs submitted already, so feel free to be artistically creative :)
• Happy to take advice re fonts/colours/printability etc.
Nice to have
• I'm not sure if "lists" are more at home on a CV than a business card, but representative services include:
• Applied electromagnetics
• RF and high speed electronics
• Signal and image processing
• Electro-optical and laser systems
• Concept-to-prototype design services
• If you're considering double sided cards, then often measuring/alignment grids/rulers feature on the back of similar cards.
• e.g. https://www.veltranoptics.example/newgrouppage9.cfm?objectgroup_id=4183
• https://www.veltranoptics.example/newgrouppage9.cfm?objectgroup_ID=4185
• ..or even a "Smith chart" (google will return lots)
• Generic images to represent a capability might work - googling images associated with keyword for each of these areas might help:
• - "passive radar", "phased array", "fdtd", "vircator"
• RF and high speed electronic design
• - "smith chart", "microstrip circuits", "dimensioned drawing", "electronic schematic"
• - "dft", "iir filter"
• - "optical cavity". "laser energy level diagram"
• Background/watermarked images outlines/wireframes/schematics would probably look OK.
Should not have
• If a list of projects/services is provided, it is important not to make the client feel that this is "all" the company can do. Engineering design is a creative discipline (like graphics :)
• Please, no stock "military" snaps like planes, missiles, etc!

```html
<!DOCTYPE html>
<html lang="en">
<head>
<meta charset="utf-8">
<title>Wombarra Devices – Business Card</title>
<link href="https://fonts.googleapis.com/css2?family=Lato:wght@400;700;900&display=swap" rel="stylesheet">
<style>
  :root {
    --navy: #1f2a5e;
    --orange: #f58220;
    --white: #ffffff;
    --page: #e9eaee;
    --shadow: rgba(20, 25, 50, 0.18);
  }
  * { margin: 0; padding: 0; box-sizing: border-box; }
  html, body {
    width: 1200px; height: 835px; overflow: hidden;
    background: var(--page);
    font-family: "Lato", sans-serif;
  }
  .card {
    position: absolute; left: 280px;
    width: 640px; height: 366px;
    border-radius: 22px; overflow: hidden;
    box-shadow: 0 8px 24px var(--shadow);
  }
  .card--front { top: 30px; background: var(--white); }
  .card--back { top: 439px; background: var(--navy); }
  .card__shapes { position: absolute; inset: 0; }

  .brand {
    position: absolute; display: flex; align-items: center; gap: 12px;
    font-weight: 900; font-size: 26px; letter-spacing: 1px; text-transform: uppercase;
  }
  .brand__dot { width: 34px; height: 34px; border-radius: 50%; }
  .card--front .brand { right: 44px; top: 40px; color: var(--navy); }
  .card--front .brand__dot { background: var(--navy); }
  .card--back .brand { left: 44px; top: 70px; color: var(--white); }
  .card--back .brand__dot { background: var(--white); }

  .person { position: absolute; left: 0; top: 166px; padding-left: 46px; }
  .person__bar { position: absolute; left: 0; top: 6px; width: 30px; height: 40px; background: var(--orange); }
  .person__name { font-weight: 900; font-size: 25px; color: var(--navy); line-height: 1.1; }
  .person__role { font-weight: 700; font-size: 17px; color: var(--orange); margin-top: 2px; }

  .contact { position: absolute; left: 46px; top: 238px; list-style: none; color: var(--navy); font-size: 16px; }
  .contact li { display: flex; align-items: center; gap: 10px; line-height: 26px; }
  .contact svg { width: 14px; height: 14px; fill: var(--orange); }

  .address {
    position: absolute; right: 40px; top: 228px; text-align: right;
    color: var(--navy); font-size: 16px; line-height: 22px;
  }

  .services {
    position: absolute; right: 30px; top: 214px; list-style: none; text-align: right;
    color: var(--navy); font-size: 17px; line-height: 24px; font-weight: 700;
  }
  .services li::after {
    content: ""; display: inline-block; width: 9px; height: 9px; margin-left: 9px;
    border-radius: 50%; background: var(--orange); vertical-align: middle;
  }
</style>
</head>
<body>

<section class="card card--front" aria-label="Business card front">
  <svg class="card__shapes" viewBox="0 0 640 366" aria-hidden="true">
    <polygon points="330,366 395,292 640,292 640,366" fill="var(--navy)"/>
    <polygon points="313,366 350,324 355,324 318,366" fill="var(--orange)"/>
  </svg>

  <div class="brand"><span class="brand__dot"></span>Wombarra Devices</div>

  <div class="person">
    <span class="person__bar"></span>
    <p class="person__name">Dr Colin Harte</p>
    <p class="person__role">R&amp;D Engineer</p>
  </div>

  <ul class="contact">
    <li>
      <svg viewBox="0 0 24 24"><path d="M6.6 10.8a15 15 0 0 0 6.6 6.6l2.2-2.2a1 1 0 0 1 1-.25 11.4 11.4 0 0 0 3.6.57 1 1 0 0 1 1 1V20a1 1 0 0 1-1 1A17 17 0 0 1 3 4a1 1 0 0 1 1-1h3.5a1 1 0 0 1 1 1c0 1.25.2 2.45.57 3.57a1 1 0 0 1-.25 1z"/></svg>
      0427 563 710
    </li>
    <li>
      <svg viewBox="0 0 24 24"><path d="M2 6a2 2 0 0 1 2-2h16a2 2 0 0 1 2 2v12a2 2 0 0 1-2 2H4a2 2 0 0 1-2-2zm2 .5V18h16V6.5l-8 5.5z"/></svg>
      colin@wombarradevices.com.au
    </li>
  </ul>

  <p class="address">PO Box XXX<br>Kelsby ACT 2917, Australia</p>
</section>

<section class="card card--back" aria-label="Business card back">
  <svg class="card__shapes" viewBox="0 0 640 366" aria-hidden="true">
    <polygon points="138,366 206,214 210,214 142,366" fill="var(--white)"/>
    <polygon points="160,366 228,214 640,172 640,366" fill="var(--white)"/>
  </svg>

  <div class="brand"><span class="brand__dot"></span>Wombarra Devices</div>

  <ul class="services">
    <li>Radar jammers,</li>
    <li>High power lasers</li>
    <li>GPS antenna design,</li>
    <li>Satellite tracking systems,</li>
    <li>Instrumentation for electrical testing,</li>
  </ul>
</section>

</body>
</html>
```